eBook-Cover für Thriller gesucht
An dieser Stelle ein großes Lob und vielen Dank an die Designerin Larosa. Auch das zweite Buchcover ist wieder überaus gelungen, eine ganz tolle Arbeit. Auch die angenehme Zusammenarbeit war mir, wie schon beim ersten Auftrag, eine Freude. Ebenso hervorzuheben ist die Schnelligkeit und Kreativität, mit der die Designerin auf Änderungswünsche reagiert. Als Auftraggeber gebe ich verdiente fünf Sterne und bin mit dem Ergebnis wirklich sehr zufrieden.
Zielgruppe
Ich bin Autor. Zielgruppe sind (anspruchsvolle) Leser/innen von Thrillern und Kriminalromanen im ebook-Bereich.
Aufgabenstellung
- Gesucht wird ein ebook-Cover für einen Thriller mit dem Titel 'Kaltgrund'
- Grobe Aufteilung siehe Skizzen
- Fokus des Covers liegt auf dem Buchtitel und dem Motiv ('Blauer Drachen')
- Hintergrund eher hell, Assoziation mit zarter Eisfläche mit angedeuteten Rissen vom Hauptmotiv ausgehend. Dadurch auch Tiefe und Dreidimensionalität. (Beispiel zum Hintergrund: 'Schattenfrist' von Heinrich Wendel, jedoch ohne Blut )
-Titelschrift groß, Stil 'gekratzt' bzw. 'gestrichelt', (Schriftart ähnlich wie Autorenname bei 'Die Schleuse' von Matthias Kolbe). Schrift groß und 'treppenförmig' neben dem Hauptmotiv angeordnet. Schriftfarbe schwarz/dunkelblau, ähnlich Hauptmotiv (Bsp.: 'Schwarzeid' von Heinrich Wendel)
Hauptmotiv ist der vom rechten Coverrand hineinragende 'Blaue Drachen' (Glaucus atlanticus, siehe hochgeladenes Beispielbild von Wissnetz)
- Schriftart von Autorenname und Genre eher klar
- eigene Detailvorschläge zur Optimierung des Ergebnisses möglich bzw. erwünscht

```html
<!DOCTYPE html>
<html lang="de">
<head>
<meta charset="utf-8">
<title>Kaltgrund – Konrad Velten</title>
<link rel="stylesheet" href="https://fonts.googleapis.com/css2?family=Cinzel:wght@400;700&family=Fredericka+the+Great&display=swap">
<style>
  :root {
    --ice-light: #eef5f8;
    --ice-mid: #b9d3de;
    --ice-deep: #5f8aa3;
    --ice-edge: #3d6580;
    --ink-navy: #121a33;
    --title-ice: #7cc3cd;
    --title-frost: #f4fafc;
    --dragon-deep: #1b2a78;
    --dragon-mid: #3e5bb5;
    --dragon-pale: #a9c4e6;
  }
  html, body {
    margin: 0;
    padding: 0;
    overflow: hidden;
    background: var(--ice-deep);
  }
  .cover {
    position: relative;
    width: 724px;
    height: 1200px;
    overflow: hidden;
    background:
      radial-gradient(ellipse 60% 45% at 48% 52%, var(--ice-light) 0%, var(--ice-mid) 55%, transparent 100%),
      radial-gradient(ellipse 80% 70% at 50% 50%, var(--ice-mid) 0%, var(--ice-deep) 85%, var(--ice-edge) 100%);
  }
  .ice-cracks {
    position: absolute;
    inset: 0;
  }
  .author {
    position: absolute;
    top: 42px;
    left: 0;
    width: 724px;
    margin: 0;
    text-align: center;
    font-family: "Cinzel", serif;
    font-weight: 400;
    font-size: 62px;
    letter-spacing: 1px;
    color: var(--ink-navy);
    line-height: 1;
    padding-left: 46px;
    box-sizing: border-box;
  }
  .blue-dragon {
    position: absolute;
    top: 70px;
    left: 255px;
    width: 469px;
    height: 600px;
  }
  .title {
    margin: 0;
    font-family: "Fredericka the Great", cursive;
    font-weight: 400;
    color: var(--title-ice);
    text-shadow:
      0 0 2px var(--ink-navy),
      1px 2px 0 rgba(18, 26, 51, 0.55),
      0 0 14px var(--title-frost),
      0 0 26px var(--title-frost);
  }
  .title-line {
    position: absolute;
    display: block;
    font-size: 190px;
    line-height: 1;
    letter-spacing: 4px;
  }
  .title-line--first { top: 320px; left: 18px; }
  .title-line--second { top: 585px; left: 150px; }
  .title-line--third { top: 808px; left: 285px; }
  .genre {
    position: absolute;
    top: 1146px;
    left: 0;
    width: 724px;
    margin: 0;
    text-align: center;
    font-family: "Cinzel", serif;
    font-weight: 700;
    font-size: 34px;
    letter-spacing: 17px;
    color: var(--ink-navy);
    line-height: 1;
  }
</style>
</head>
<body>
  <main class="cover">
    <svg class="ice-cracks" width="724" height="1200" viewBox="0 0 724 1200" aria-hidden="true">
      <g fill="none" stroke="#4d6878" stroke-width="1.2" opacity="0.6">
        <path d="M470 110 L462 160 L480 215 L455 260 L470 300"/>
        <path d="M440 560 L455 640 L470 700 L458 760 L475 820 L465 900 L450 990 L462 1080 L455 1200"/>
        <path d="M470 700 L520 740 L600 790 L690 800"/>
        <path d="M0 1020 L60 930 L110 840 L160 790 L220 740"/>
        <path d="M120 220 L210 235 L280 250 L350 285"/>
        <path d="M600 920 L640 1000 L620 1090 L660 1160"/>
      </g>
    </svg>

    <p class="author">KONRAD VELTEN</p>

    <svg class="blue-dragon" viewBox="0 0 469 600" role="img" aria-label="Blauer Drachen (Glaucus atlanticus) ragt vom rechten Rand ins Eis">
      <defs>
        <radialGradient id="dragon-tone" cx="55%" cy="45%" r="60%">
          <stop offset="0%" stop-color="var(--dragon-pale)"/>
          <stop offset="45%" stop-color="var(--dragon-mid)"/>
          <stop offset="100%" stop-color="var(--dragon-deep)" stop-opacity="0"/>
        </radialGradient>
      </defs>
      <ellipse cx="260" cy="310" rx="250" ry="250" fill="url(#dragon-tone)" opacity="0.85"/>
    </svg>

    <h1 class="title" aria-label="Kaltgrund">
      <span class="title-line title-line--first" aria-hidden="true">KAL</span>
      <span class="title-line title-line--second" aria-hidden="true">TGR</span>
      <span class="title-line title-line--third" aria-hidden="true">UND</span>
    </h1>

    <p class="genre">THRILLER</p>
  </main>
</body>
</html>
```